Suite Refresh Partners - Tabletop Display

We need a 5'x5' trade show display for a hotel renovation company named "Suite Refresh Partners." Suite Refresh Partners is the most complete authority on hotel renovation in the country, and we're the only 100% turn-key renovator in Colorado. With one phone call, we deliver an approved design, FF&E purchasing, logistics, construction, installation, and warranty administration. The design needs to convey professionalism. Our goal is to help our clients reduce costs and reduce stress while achieving the best results. The colors should align with the attached brochure for our Raleigh office.

Target Market(s)

Hotel owners and general managers

Industry/Entity Type

Design Agency

Colors
3277b5
85acd3
cfdeed

Requirements
Must have
• Our product is a blend of design and construction. I need to convey our services and attention to detail without seeming salesy, bold, or aggressive. The goal is to convey confidence and help to relax our potential client base.
Nice to have
• Possibly one or more photos of completed projects. Not sure if exterior, lobby, or guest room photos would be best. I can send files via dropbox if that's helpful.
Should not have
• I've included a photo of the old display at a trade show. I strongly dislike the yellow and red on the display. Please try to stick to the color palette of the attached brochure.

```html
<!DOCTYPE html>
<html lang="en">
<head>
<meta charset="utf-8">
<title>Suite Refresh Partners – Tabletop Display</title>
<link rel="stylesheet" href="https://fonts.googleapis.com/css2?family=Inter:wght@300;400;700&family=Raleway:wght@400&display=swap">
<style>
  :root {
    --brand-blue: #3264b0;
    --brand-cyan: #1ec2e2;
    --rule-gray: #b9b9b9;
    --body-gray: #5a5a5a;
    --ink: #1f1f1f;
    --paper: #ffffff;
  }
  * { margin: 0; padding: 0; box-sizing: border-box; }
  html, body { width: 1200px; height: 1200px; overflow: hidden; background: var(--paper); }
  .display {
    position: relative;
    width: 1200px;
    height: 1200px;
    background: var(--paper);
    font-family: "Inter", Helvetica, Arial, sans-serif;
    overflow: hidden;
  }
  .display__graphics { position: absolute; inset: 0; }

  .brand {
    position: absolute;
    left: 61px;
    top: 92px;
    display: flex;
    align-items: center;
    gap: 14px;
  }
  .brand__square { width: 22px; height: 22px; background: var(--brand-blue); }
  .brand__name {
    font-weight: 700;
    font-size: 30px;
    line-height: 1.15;
    color: var(--brand-blue);
  }

  .headline {
    position: absolute;
    left: 95px;
    top: 710px;
    color: var(--brand-blue);
    font-weight: 300;
    font-size: 68px;
    line-height: 1;
    letter-spacing: -1px;
  }
  .headline__line { display: block; height: 84px; }
  .headline__line--first { height: 88px; }
  .headline strong { font-weight: 700; }
  .headline__rule {
    position: absolute;
    left: 95px;
    top: 788px;
    width: 633px;
    height: 4px;
    background: var(--rule-gray);
  }

  .services {
    position: absolute;
    top: 1008px;
    left: 0;
    width: 100%;
    list-style: none;
    font-size: 27px;
    line-height: 34px;
    color: var(--body-gray);
  }
  .services__item { position: absolute; white-space: nowrap; }
  .services__item:nth-child(1) { left: 95px; }
  .services__item:nth-child(2) { left: 290px; }
  .services__item:nth-child(3) { left: 526px; }
  .services__item:nth-child(4) { left: 771px; }

  .contact__phone {
    position: absolute;
    left: 95px;
    top: 1133px;
    font-size: 35px;
    font-weight: 300;
    color: var(--brand-blue);
  }
  .contact__web {
    position: absolute;
    left: 735px;
    top: 1138px;
    font-family: "Raleway", Helvetica, Arial, sans-serif;
    font-size: 31px;
    color: var(--ink);
  }
</style>
</head>
<body>
<main class="display">
  <svg class="display__graphics" width="1200" height="1200" viewBox="0 0 1200 1200" aria-hidden="false">
    <defs>
      <linearGradient id="steel-top" x1="0" y1="1" x2="1" y2="0">
        <stop offset="0" stop-color="#3a3a3a"/>
        <stop offset="0.6" stop-color="#9a9a9a"/>
        <stop offset="1" stop-color="#ffffff"/>
      </linearGradient>
      <linearGradient id="steel-bottom" x1="0" y1="0" x2="1" y2="1">
        <stop offset="0" stop-color="#ffffff"/>
        <stop offset="1" stop-color="#4a4a4a"/>
      </linearGradient>
      <linearGradient id="lobby-tones" x1="0" y1="0" x2="1" y2="1">
        <stop offset="0" stop-color="#6b5a4a"/>
        <stop offset="0.45" stop-color="#a8834f"/>
        <stop offset="0.75" stop-color="#c9a56a"/>
        <stop offset="1" stop-color="#8c7a68"/>
      </linearGradient>
    </defs>

    <!-- steel accent wedges -->
    <polygon class="accent-steel" points="190,405 635,110 720,160 300,400" fill="url(#steel-top)"/>
    <polygon class="accent-steel" points="545,695 976,851 900,858 560,720" fill="url(#steel-bottom)"/>

    <!-- project photo area -->
    <g role="img" aria-label="Photo of a renovated hotel lobby with stone fireplace, lounge chairs and warm lighting">
      <polygon points="330,542 880,290 1200,196 1200,789 976,851" fill="url(#lobby-tones)"/>
    </g>

    <!-- main diagonal band -->
    <polygon class="band-blue" points="0,498 880,94 880,290 0,694" fill="var(--brand-blue)"/>

    <!-- translucent cyan overlay -->
    <polygon class="overlay-cyan" points="833,180 1200,0 1200,196 833,373" fill="var(--brand-cyan)" opacity="0.8"/>

    <!-- lower right wedge -->
    <polygon class="wedge-blue" points="788,918 1200,789 1200,1074" fill="var(--brand-blue)"/>
  </svg>

  <div class="brand">
    <span class="brand__square"></span>
    <span class="brand__name">Suite Refresh<br>Partners</span>
  </div>

  <h1 class="headline">
    <span class="headline__line headline__line--first">A COMPLETE</span>
    <span class="headline__line">RENOVATION WITH</span>
    <span class="headline__line">JUST <strong>ONE CALL!</strong></span>
  </h1>
  <div class="headline__rule"></div>

  <ul class="services">
    <li class="services__item">Planning<br>Design</li>
    <li class="services__item">Specification<br>FF&amp;E</li>
    <li class="services__item">Logistics<br>Construction</li>
    <li class="services__item">Installation<br>Warranty Administration</li>
  </ul>

  <p class="contact__phone">Ph: 919-555-0142 / 919-555-0187</p>
  <p class="contact__web">www.suiterefresh.com</p>
</main>
</body>
</html>
```